WordPress website design for wealth management company

A modern clean look website for a service company. This is mostly for information only, with a form to capture prospect contact information and schedule a 15 minutes call. There will be several static pages describe what services we offer, how we are different, and a blog section for posting articles and share resources. A section for client testimonials.
I want a website that is easy to understand and maintain. No proprietary plugins that cost extra. The main thing I need help is the visual layout / color palette that present a clean and professional look, select the suitable stock photos that convey the image of trust, professional, innovative, and high service.
Some websites with style I like include the following
- https://www.halvorbrook.com/
- https://www.trivanplanningworks.com/
- https://morvellfunds.com/private-equity-partners/
Also some websites in other industries with clean modern look
- https://zentrell.com/
- https://quovra.com/
- https://www.plumtorvik.com/
I want the end product to be a fully functional website that I can upload into web hosting service I use and I can easily add content and maintain myself in the future.

```html
<!DOCTYPE html>
<html lang="en">
<head>
<meta charset="utf-8">
<title>Brenmoor Wealth</title>
<link href="https://fonts.googleapis.com/css2?family=Montserrat:wght@600;700;800&family=Roboto:wght@400;500;700&display=swap" rel="stylesheet">
<style>
:root{
  --purple:#5b2a8c;
  --purple-dark:#4a2176;
  --gold:#f6b321;
  --gold-dark:#d08a12;
  --ink:#222;
  --muted:#6b6b6b;
  --grey:#f3f3f3;
  --white:#fff;
}
*{box-sizing:border-box;margin:0;padding:0}
html,body{width:1200px;height:4208px;overflow:hidden}
body{position:relative;font-family:'Roboto',Arial,sans-serif;color:var(--ink);background:var(--white)}
.abs{position:absolute}
h1,h2,h3{font-family:'Montserrat',Arial,sans-serif;font-weight:700}
.btn{position:absolute;display:flex;align-items:center;justify-content:center;gap:8px;border-radius:30px;font-family:'Montserrat',Arial,sans-serif;font-weight:700;font-size:14px;color:var(--white);background:linear-gradient(90deg,var(--purple),var(--gold-dark));text-transform:uppercase}
.btn .dot{width:13px;height:13px;border-radius:50%;background:currentColor;display:inline-block;position:relative}
.btn .dot::after{content:"";position:absolute;left:4px;top:3px;border-left:5px solid var(--purple);border-top:3.5px solid transparent;border-bottom:3.5px solid transparent}
.btn.light .dot::after{border-left-color:var(--white)}
.photo{position:absolute}
/* header */
.top-bar{left:0;top:0;width:1200px;height:3px;background:var(--gold)}
.brand{left:140px;top:12px;width:170px;text-align:center}
.brand-mark{width:50px;height:50px;border-radius:50%;border:5px solid var(--purple);margin:0 auto 6px}
.brand-name{font-family:'Montserrat',Arial,sans-serif;font-weight:700;color:var(--purple);font-size:20px;letter-spacing:2px}
.contact-chip{top:18px;display:flex;gap:12px;align-items:center}
.chip-icon{width:36px;height:36px;border-radius:50%;display:flex;align-items:center;justify-content:center}
.chip-label{font-size:11px;color:var(--muted)}
.chip-value{font-size:14px;font-weight:500}
.nav{left:430px;top:75px;width:770px;height:40px;background:var(--purple);display:flex;align-items:center}
.nav a{color:var(--white);font-family:'Montserrat',Arial,sans-serif;font-weight:700;font-size:13px;text-decoration:none;padding:0 17px;height:40px;line-height:40px}
.nav a.active{background:var(--gold);padding:0 24px 0 30px;clip-path:polygon(18px 0,100% 0,100% 100%,0 100%)}
/* hero */
.hero-photo{left:0;top:115px;width:1200px;height:560px;background:linear-gradient(100deg,#6b6a6c,#a99b90 45%,#8e7d6f 75%,#5d5350)}
.hero-title{left:143px;top:282px;color:var(--white);font-size:36px}
.hero-text{left:145px;top:335px;width:340px;color:var(--white);font-weight:500;font-size:15px;line-height:25px}
/* sections */
.section-title{position:absolute;left:0;width:1200px;text-align:center;font-size:35px;color:#111}
.body-text{font-size:13px;line-height:24px;color:var(--muted)}
.card{position:absolute;background:var(--white);box-shadow:0 2px 10px rgba(0,0,0,.12)}
.card h3{font-family:'Roboto',Arial,sans-serif;font-weight:700;font-size:17px;text-align:center}
.card p{font-size:12.5px;line-height:20px;color:var(--muted);text-align:center}
.quote{font-family:'Montserrat',Arial,sans-serif;font-weight:800;font-size:80px;color:var(--purple);text-align:center;line-height:80px;height:50px;overflow:hidden}
.field{position:absolute;background:#f1f1f1;border-radius:2px;font-size:11px;color:#777;padding:0 14px;display:flex;align-items:center}
.field.area{align-items:flex-start;padding-top:28px}
.info-row{position:absolute;left:175px;display:flex;gap:20px;color:var(--white)}
.ring{width:46px;height:46px;border:1.5px solid var(--white);border-radius:50%;display:flex;align-items:center;justify-content:center;flex:none}
.info-row b{font-size:15px;display:block;margin-bottom:6px}
.info-row span{font-size:14px;line-height:22px}
.footer-nav{left:335px;top:3968px;font-size:14px;color:#444}
.social{width:32px;height:32px;border-radius:50%;background:var(--purple);position:absolute;top:3961px}
.foot-item{position:absolute;top:4040px;display:flex;gap:12px;font-size:13px}
.foot-item .ic{width:28px;height:28px;border-radius:50%;background:var(--purple);flex:none}
.foot-item b{display:block;font-size:14px;margin-bottom:3px}
.foot-item span{color:var(--muted);font-size:12.5px;line-height:18px}
.stars{position:absolute;color:var(--gold);font-size:22px;letter-spacing:-2px;width:100px;text-align:center}
.avatar{position:absolute;width:70px;height:70px;border-radius:50%;border:3px solid #fff}
</style>
</head>
<body>

<!-- Header -->
<div class="abs top-bar"></div>
<div class="abs brand">
  <div class="brand-mark"></div>
  <div class="brand-name">BRENMOOR</div>
</div>
<div class="abs contact-chip" style="left:610px">
  <div class="chip-icon" style="background:var(--gold)"><svg width="18" height="14" viewBox="0 0 18 14"><rect x="1" y="1" width="16" height="12" rx="1" fill="none" stroke="#fff" stroke-width="2"/><path d="M1 2l8 6 8-6" fill="none" stroke="#fff" stroke-width="2"/></svg></div>
  <div><div class="chip-label">Email Us On</div><div class="chip-value">info@brenmoor.com</div></div>
</div>
<div class="abs contact-chip" style="left:860px">
  <div class="chip-icon" style="background:var(--purple)"><svg width="18" height="18" viewBox="0 0 24 24"><path d="M6.6 10.8a15 15 0 006.6 6.6l2.2-2.2a1 1 0 011-.25 11 11 0 003.5.56 1 1 0 011 1V20a1 1 0 01-1 1A17 17 0 013 4a1 1 0 011-1h3.5a1 1 0 011 1 11 11 0 00.56 3.5 1 1 0 01-.25 1z" fill="#fff"/></svg></div>
  <div><div class="chip-label">Call Us Today</div><div class="chip-value" style="font-size:18px;font-weight:700">+1-555-014-2297</div></div>
</div>
<nav class="abs nav">
  <a class="active">HOME</a><a>ABOUT US</a><a>OUR SERVICES</a><a>TESTIMONIALS</a><a>BLOG</a><a>CONTACT US</a>
</nav>

<!-- Hero -->
<div class="photo hero-photo" role="img" aria-label="Happy family of four on a sofa giving thumbs up"></div>
<div class="abs" style="left:0;top:115px;width:560px;height:560px;background:linear-gradient(90deg,rgba(40,30,40,.55),rgba(40,30,40,0))"></div>
<h1 class="abs hero-title">BRENMOOR WEALTH</h1>
<p class="abs hero-text">Lorem ipsum dolor sit consectetur adipiscing elit, sed do eiusmod tempor ut labore.</p>
<div class="btn" style="left:146px;top:412px;width:175px;height:38px">GET STARTED <i class="dot"></i></div>
<svg class="abs" style="left:0;top:650px" width="1200" height="45" viewBox="0 0 1200 45">
  <polygon points="140,15 1110,15 1100,22 120,22" fill="var(--gold)"/>
  <polygon points="190,5 1040,5 1030,15 180,15" fill="var(--purple)"/>
  <polygon points="45,22 1180,22 1160,40 25,40" fill="var(--purple)"/>
</svg>

<!-- About -->
<div class="photo" style="left:143px;top:755px;width:345px;height:345px;border-radius:50%;background:radial-gradient(circle,#e8d3a0,#b9a0cf 60%,#7e55a8)" role="img" aria-label="Business team reviewing growth charts"></div>
<h2 class="abs" style="left:593px;top:763px;font-size:35px">ABOUT <span style="color:var(--purple)">US</span></h2>
<p class="abs body-text" style="left:593px;top:828px;width:463px">Lorem ipsum dolor sit amet, consectetur adipiscing elit, sed do eiusmod tempor incididunt ut labore et dolore magna aliqua. Ut enim ad minim veniam, quis nostrud exercitation ullamco laboris nisi ut aliquip ex ea commodo consequat. Duis aute irure dolor in reprehenderit in voluptate velit esse cillum dolore eu fugiat nulla pariatur.</p>
<p class="abs body-text" style="left:593px;top:957px;width:463px">Sed ut perspiciatis unde omnis iste natus error sit voluptatem accusantium veritatis et quasi architecto beatae vitae dicta sunt explicabo.</p>
<div class="btn" style="left:594px;top:1039px;width:166px;height:42px">READ MORE <i class="dot"></i></div>

<!-- Services -->
<div class="abs" style="left:0;top:1165px;width:1200px;height:647px;background:var(--grey)"></div>
<h2 class="section-title" style="top:1240px">OUR SERVICES</h2>
<svg class="abs" style="left:110px;top:1288px" width="975" height="440" viewBox="0 0 975 440">
  <polygon points="15,0 330,0 320,12 5,12" fill="#fff"/><polygon points="335,0 650,0 640,12 325,12" fill="#fff"/><polygon points="655,0 975,0 965,12 645,12" fill="#fff"/>
  <polygon points="15,425 330,425 320,437 5,437" fill="#fff"/><polygon points="335,425 650,425 640,437 325,437" fill="#fff"/><polygon points="655,425 975,425 965,437 645,437" fill="#fff"/>
</svg>
<div class="card" style="left:138px;top:1303px;width:287px;height:412px">
  <div class="photo" style="left:5px;top:5px;width:277px;height:208px;background:linear-gradient(135deg,#d6d2cc,#8c7d70)" role="img" aria-label="Financial advisor helping a client at a laptop"></div>
  <h3 style="margin-top:238px">LOREM IPSUM DOLOR</h3>
  <p style="margin:6px 12px 0">Sed ut perspiciatis unde omnis iste natus error sit voluptatem accusantium doloremque laudantium, totam rem aperiam.</p>
  <div class="btn" style="left:66px;top:345px;width:155px;height:38px;font-size:12px">LEARN MORE <i class="dot"></i></div>
</div>
<div class="card" style="left:457px;top:1303px;width:287px;height:412px">
  <div class="photo" style="left:5px;top:5px;width:277px;height:208px;background:linear-gradient(135deg,#dfe4ea,#9aa8b8)" role="img" aria-label="Professional holding a tablet in a bright office"></div>
  <h3 style="margin-top:238px">LOREM IPSUM DOLOR</h3>
  <p style="margin:6px 12px 0">Sed ut perspiciatis unde omnis iste natus error sit voluptatem accusantium doloremque laudantium, totam rem aperiam.</p>
  <div class="btn" style="left:66px;top:345px;width:155px;height:38px;font-size:12px">LEARN MORE <i class="dot"></i></div>
</div>
<div class="card" style="left:776px;top:1303px;width:287px;height:412px">
  <div class="photo" style="left:5px;top:5px;width:277px;height:208px;background:linear-gradient(135deg,#e4e6ea,#3d4d6a)" role="img" aria-label="Advisor in a suit reviewing documents with a colleague"></div>
  <h3 style="margin-top:238px">LOREM IPSUM DOLOR</h3>
  <p style="margin:6px 12px 0">Sed ut perspiciatis unde omnis iste natus error sit voluptatem accusantium doloremque laudantium, totam rem aperiam.</p>
  <div class="btn" style="left:66px;top:345px;width:155px;height:38px;font-size:12px">LEARN MORE <i class="dot"></i></div>
</div>

<!-- Different -->
<div class="abs" style="left:0;top:1812px;width:1200px;height:453px;background:var(--purple)"></div>
<div class="photo" style="left:570px;top:1812px;width:630px;height:453px;background:linear-gradient(120deg,#ecebe8,#c9c3bb 60%,#8f8173);clip-path:polygon(90px 0,100% 0,100% 100%,90px 100%,20px 226px)" role="img" aria-label="Calm woman meditating in front of a task board"></div>
<svg class="abs" style="left:570px;top:1812px" width="100" height="453" viewBox="0 0 100 453"><polyline points="92,0 22,226 92,453" fill="none" stroke="var(--gold)" stroke-width="10"/></svg>
<h2 class="abs" style="left:143px;top:1870px;color:#fff;font-size:33px">HOW WE ARE DIFFERENT</h2>
<p class="abs body-text" style="left:143px;top:1930px;width:370px;color:#fff">Lorem ipsum dolor sit amet, consectetur adipiscing elit, sed do eiusmod tempor incididunt ut labore et dolore magna aliqua. Ut enim ad minim veniam, quis nostrud exercitation ullamco laboris nisi ut aliquip ex ea commodo.</p>
<p class="abs body-text" style="left:143px;top:2034px;width:370px;color:#fff">Sed ut perspiciatis unde omnis iste natus error sit voluptatem accusantium doloremque laudantium, totam rem aperiam, eaque ipsa quae ab illo inventore veritatis et quasi architecto beatae vitae dicta sunt explicabo.</p>
<div class="btn light" style="left:143px;top:2160px;width:162px;height:42px;background:#fff;color:var(--purple)">LEARN MORE <i class="dot"></i></div>

<!-- Blog -->
<h2 class="section-title" style="top:2330px">BLOG</h2>
<div class="card" style="left:143px;top:2398px;width:288px;height:362px;border-radius:4px">
  <div class="photo" style="left:7px;top:7px;width:274px;height:190px;background:linear-gradient(135deg,#e2e5e8,#3f5a78)" role="img" aria-label="Two professionals reviewing a tablet together"></div>
  <div style="margin-top:220px;text-align:center;font-size:12.5px;color:var(--purple)">&#9638; February 2, 2021</div>
  <h3 style="font-size:15px;margin-top:6px">Lorem ipsum dolor sit amet,</h3>
  <p style="margin:12px 14px 0">Sed ut perspiciatis unde omnis iste natus sit voluptatem accusantium</p>
  <div style="text-align:center;margin-top:12px;font-weight:700;font-size:13px;color:var(--purple)">READ MORE &#10148;</div>
</div>
<div class="card" style="left:456px;top:2398px;width:288px;height:362px;border-radius:4px">
  <div class="photo" style="left:7px;top:7px;width:274px;height:190px;background:linear-gradient(135deg,#eef0f2,#5b6470)" role="img" aria-label="Speaker presenting to an audience"></div>
  <div style="margin-top:220px;text-align:center;font-size:12.5px;color:var(--purple)">&#9638; February 2, 2021</div>
  <h3 style="font-size:15px;margin-top:6px">Lorem ipsum dolor sit amet,</h3>
  <p style="margin:12px 14px 0">Sed ut perspiciatis unde omnis iste natus sit voluptatem accusantium</p>
  <div style="text-align:center;margin-top:12px;font-weight:700;font-size:13px;color:var(--purple)">READ MORE &#10148;</div>
</div>
<div class="card" style="left:769px;top:2398px;width:288px;height:362px;border-radius:4px">
  <div class="photo" style="left:7px;top:7px;width:274px;height:190px;background:linear-gradient(135deg,#e9ebee,#8a8f96)" role="img" aria-label="Advisor on the phone at a desk"></div>
  <div style="margin-top:220px;text-align:center;font-size:12.5px;color:var(--purple)">&#9638; February 2, 2021</div>
  <h3 style="font-size:15px;margin-top:6px">Lorem ipsum dolor sit amet,</h3>
  <p style="margin:12px 14px 0">Sed ut perspiciatis unde omnis iste natus sit voluptatem accusantium</p>
  <div style="text-align:center;margin-top:12px;font-weight:700;font-size:13px;color:var(--purple)">READ MORE &#10148;</div>
</div>

<!-- Testimonials -->
<div class="abs" style="left:0;top:2838px;width:1200px;height:545px;background:var(--grey)"></div>
<h2 class="section-title" style="top:2880px">WHAT OUR CUSTOMERS SAY</h2>
<div class="card" style="left:143px;top:3008px;width:290px;height:280px;box-shadow:none">
  <div class="quote" style="margin-top:20px">&ldquo;</div>
  <p style="margin:18px 16px 0;text-align:justify;text-align-last:center;line-height:21px">Lorem ipsum dolor sit amet, consectetur adipiscing elit, sed do eiusmod tempor incididunt ut labore et dolore magna aliqua. Ut enim ad minim veniam, quis nostrud exercitation ullamco.</p>
  <div class="stars" style="left:95px;top:202px">&#9733;&#9733;&#9733;&#9733;&#9733;</div>
  <div class="avatar" style="left:110px;top:225px;background:#c9b8a8" role="img" aria-label="Client portrait"></div>
</div>
<div class="card" style="left:453px;top:2970px;width:292px;height:280px;box-shadow:none">
  <div class="quote" style="margin-top:20px">&ldquo;</div>
  <p style="margin:18px 16px 0;text-align:justify;text-align-last:center;line-height:21px">Lorem ipsum dolor sit amet, consectetur adipiscing elit, sed do eiusmod tempor incididunt ut labore et dolore magna aliqua. Ut enim ad minim veniam, quis nostrud exercitation ullamco.</p>
  <div class="stars" style="left:96px;top:202px">&#9733;&#9733;&#9733;&#9733;&#9733;</div>
  <div class="avatar" style="left:111px;top:225px;background:#b7c3cf" role="img" aria-label="Client portrait"></div>
</div>
<div class="card" style="left:763px;top:3008px;width:290px;height:280px;box-shadow:none">
  <div class="quote" style="margin-top:20px">&ldquo;</div>
  <p style="margin:18px 16px 0;text-align:justify;text-align-last:center;line-height:21px">Lorem ipsum dolor sit amet, consectetur adipiscing elit, sed do eiusmod tempor incididunt ut labore et dolore magna aliqua. Ut enim ad minim veniam, quis nostrud exercitation ullamco.</p>
  <div class="stars" style="left:95px;top:202px">&#9733;&#9733;&#9733;&#9733;&#9733;</div>
  <div class="avatar" style="left:110px;top:225px;background:#8d8f99" role="img" aria-label="Client portrait"></div>
</div>
<svg class="abs" style="left:580px;top:3322px" width="40" height="14" viewBox="0 0 40 14"><circle cx="6" cy="7" r="4" fill="#111"/><circle cx="20" cy="7" r="5" fill="#fff" stroke="#111"/><circle cx="34" cy="7" r="4" fill="#111"/></svg>

<!-- Schedule -->
<div class="abs" style="left:0;top:3383px;width:1200px;height:470px;background:linear-gradient(90deg,var(--purple-dark),var(--purple) 50%,var(--purple-dark))"></div>
<h2 class="section-title" style="top:3430px;color:#fff">SCHEDULE A 15 MINUTES CALL</h2>
<div class="info-row" style="top:3545px"><div class="ring"><svg width="18" height="22" viewBox="0 0 18 22"><path d="M9 1a7 7 0 017 7c0 5-7 13-7 13S2 13 2 8a7 7 0 017-7z" fill="none" stroke="#fff" stroke-width="1.5"/><circle cx="9" cy="8" r="2.5" fill="none" stroke="#fff" stroke-width="1.5"/></svg></div><div><b>Address</b><span>651 ,Lorem ipsum dolor sit<br>consectetur adipiscing.</span></div></div>
<div class="info-row" style="top:3640px"><div class="ring"><svg width="20" height="20" viewBox="0 0 24 24"><path d="M6.6 10.8a15 15 0 006.6 6.6l2.2-2.2a1 1 0 011-.25 11 11 0 003.5.56 1 1 0 011 1V20a1 1 0 01-1 1A17 17 0 013 4a1 1 0 011-1h3.5a1 1 0 011 1 11 11 0 00.56 3.5 1 1 0 01-.25 1z" fill="none" stroke="#fff" stroke-width="1.5"/></svg></div><div><b>Phone Number</b><span>+1-555-014-2297</span></div></div>
<div class="info-row" style="top:3714px"><div class="ring"><svg width="20" height="16" viewBox="0 0 18 14"><rect x="1" y="1" width="16" height="12" fill="none" stroke="#fff" stroke-width="1.3"/><path d="M1 1l8 7 8-7" fill="none" stroke="#fff" stroke-width="1.3"/></svg></div><div><b>Email</b><span>info@brenmoor.com</span></div></div>
<div class="field" style="left:530px;top:3534px;width:232px;height:38px">&#9786;&nbsp; Name</div>
<div class="field" style="left:791px;top:3534px;width:232px;height:38px">&#9990;&nbsp; Phone Number</div>
<div class="field" style="left:530px;top:3588px;width:232px;height:38px">&#9993;&nbsp; Email Address</div>
<div class="field" style="left:791px;top:3588px;width:232px;height:38px">&#9998;&nbsp; Subject</div>
<div class="field area" style="left:530px;top:3641px;width:493px;height:80px">&#9998;&nbsp; Messagge</div>
<div class="btn" style="left:532px;top:3749px;width:106px;height:36px;background:#fff;color:var(--purple);font-size:13px">SUBMIT</div>
<svg class="abs" style="left:0;top:3845px" width="1200" height="45" viewBox="0 0 1200 45">
  <polygon points="0,0 1200,0 1180,12 20,12" fill="var(--purple)"/>
  <polygon points="120,12 1110,12 1100,20 130,20" fill="var(--gold)"/>
  <polygon points="185,20 1040,20 1030,30 195,30" fill="var(--purple)"/>
</svg>

<!-- Footer -->
<div class="abs brand" style="left:135px;top:3925px;width:120px">
  <div class="brand-mark" style="width:38px;height:38px;border-width:4px"></div>
  <div class="brand-name" style="font-size:16px">BRENMOOR</div>
</div>
<div class="abs footer-nav">Home &nbsp;&nbsp;|&nbsp;&nbsp; About Us &nbsp;&nbsp;|&nbsp;&nbsp; Our Services &nbsp;&nbsp;|&nbsp;&nbsp; Testimonials &nbsp;&nbsp;|&nbsp;&nbsp; Blog &nbsp;&nbsp;|&nbsp;&nbsp; Contact Us</div>
<div class="social" style="left:930px"></div><div class="social" style="left:974px"></div><div class="social" style="left:1019px"></div>
<div class="abs" style="left:143px;top:4017px;width:914px;height:1px;background:#e3e3e3"></div>
<div class="foot-item" style="left:193px;top:4025px"><div class="ic"></div><div><b>Address</b><span>651 ,Lorem ipsum dolor sit amet,<br>consectetur adipiscing</span></div></div>
<div class="foot-item" style="left:470px"><div class="ic"></div><div><b>Fax</b><span>123 456 7890</span></div></div>
<div class="foot-item" style="left:658px"><div class="ic"></div><div><b>Phone</b><span>+1-555-014-2297</span></div></div>
<div class="foot-item" style="left:840px"><div class="ic"></div><div><b>Email</b><span>info@brenmoor.com</span></div></div>
<div class="abs" style="left:143px;top:4122px;width:914px;height:1px;background:#e3e3e3"></div>
<div class="abs" style="left:0;top:4150px;width:1200px;text-align:center;font-size:13.5px;color:#555">&copy; 2023 Brenmoor. All Rights Reserved &nbsp;&nbsp;|&nbsp;&nbsp; Privacy Policy &nbsp;&nbsp;|&nbsp;&nbsp; Terms &amp; Condition</div>

</body>
</html>
```